Vehicle accessory sales website

We need a refreshed design for our vehicle accessory. This website is used to select vehicle year, make, model, trim and then displays products available for the vehicle you selected. The design needs to be responsive over mobile, tablet and desktop.

Current site: https://kelvorautoparts.example/vehicle-search/

We are only looking for an updated UI on the vehcile search function, not the website itself.

I want one full screen that is a Year, Make, Model and Trim Selection, this is a stamdalone page with no header, not a website page.

Then a screen that shows the vehicle selected at the top (Not a vehicle image) and the available product categories.

Then a screen that still shows the products avaiable after selecting the category

Then a product pop up

Then a checkout screen

Target Market(s)

Car dealership customers and salespeople

Industry/Entity Type

Automotive accessories

Number of Pages Required

3 page

Requirements
Must have
• Vehicle selection page, main category page, product page after category has been selected, product pop up and checkout screen

```html
<!DOCTYPE html>
<html lang="en">
<head>
<meta charset="UTF-8">
<title>Powder Coat Wheels - 4 Wheels</title>
<link href="https://fonts.googleapis.com/css2?family=Open+Sans:ital,wght@0,400;0,600;0,700;1,800&family=Crimson+Text:wght@400&display=swap" rel="stylesheet">
<style>
  :root {
    --page-bg: #ffffff;
    --card-bg: #ffffff;
    --ink: #0d0d0d;
    --ink-soft: #1f1f1f;
    --muted: #6f6f6f;
    --muted-light: #8c8c8c;
    --label: #5a5a5a;
    --border: #c4c4c4;
    --star: #f6c444;
    --button-dark: #000000;
    --button-light: #ffffff;
    --photo-edge: #3a3a3a;
    --photo-mid: #8d9093;
    --photo-light: #c2c4c6;
    --photo-dark: #141414;
  }
  * { box-sizing: border-box; margin: 0; padding: 0; }
  html, body {
    width: 1200px;
    height: 2866px;
    overflow: hidden;
    background: var(--page-bg);
    font-family: "Open Sans", Arial, sans-serif;
    color: var(--ink);
  }
  .product-card {
    position: absolute;
    left: 80px;
    top: 80px;
    width: 1040px;
    height: 2722px;
    background: var(--card-bg);
    border-radius: 38px;
    overflow: hidden;
    box-shadow: 0 6px 40px rgba(0, 0, 0, 0.10);
  }
  .product-media {
    position: absolute;
    left: 0; top: 0;
    width: 1040px;
    height: 1047px;
    background: linear-gradient(90deg, var(--photo-edge) 0%, var(--photo-mid) 12%, var(--photo-light) 30%, #a9abad 49.8%, #1b1b1b 50%, var(--photo-dark) 72%, #2b2b2b 100%);
  }
  .media-label {
    position: absolute;
    top: 6px;
    font-family: "Crimson Text", Georgia, serif;
    font-size: 108px;
    line-height: 1;
    color: #ffffff;
    -webkit-text-stroke: 4px #1a1a1a;
    paint-order: stroke fill;
  }
  .media-label--before { left: 26px; }
  .media-label--after { right: 28px; }

  .block { position: absolute; left: 80px; right: 80px; }

  .product-category {
    top: 1112px;
    font-size: 40px;
    line-height: 48px;
    font-weight: 600;
    color: var(--label);
    letter-spacing: 0.5px;
  }
  .product-title {
    top: 1202px;
    font-size: 57px;
    line-height: 66px;
    font-weight: 800;
    font-style: italic;
    color: var(--ink);
  }
  .product-part {
    top: 1291px;
    font-size: 34px;
    line-height: 44px;
    color: var(--muted-light);
  }
  .product-price {
    top: 1372px;
    display: flex;
    align-items: baseline;
    gap: 26px;
  }
  .price-current {
    font-size: 114px;
    line-height: 130px;
    font-weight: 600;
    color: var(--ink);
  }
  .price-original {
    font-size: 58px;
    font-weight: 600;
    color: var(--muted-light);
  }
  .product-description {
    top: 1549px;
    font-size: 42px;
    line-height: 70px;
    color: var(--ink-soft);
  }
  .feature-list {
    top: 1967px;
    list-style: none;
    padding-left: 30px;
  }
  .feature-list li {
    font-size: 42px;
    line-height: 70px;
    font-weight: 700;
    color: var(--ink);
    position: relative;
    padding-left: 35px;
  }
  .feature-list li::before {
    content: "";
    position: absolute;
    left: 0;
    top: 30px;
    width: 13px;
    height: 13px;
    border-radius: 50%;
    background: var(--ink);
  }
  .product-rating {
    top: 2312px;
    height: 64px;
    display: flex;
    align-items: center;
    top: 2214px;
  }
  .rating-stars { display: flex; gap: 22px; margin-right: 40px; }
  .rating-stars svg { width: 60px; height: 58px; display: block; }
  .rating-count { font-size: 42px; color: var(--muted); }

  .purchase-label {
    position: absolute;
    top: 2340px;
    font-size: 40px;
    line-height: 48px;
    font-weight: 600;
    color: var(--label);
  }
  .purchase-label--quantity { left: 80px; }
  .purchase-label--total { right: 80px; }

  .quantity-stepper {
    position: absolute;
    left: 80px;
    top: 2409px;
    width: 274px;
    height: 82px;
    border: 2px solid var(--border);
    border-radius: 6px;
    display: flex;
  }
  .stepper-button {
    width: 80px;
    display: flex;
    align-items: center;
    justify-content: center;
  }
  .stepper-button svg { width: 32px; height: 32px; }
  .stepper-value {
    flex: 1;
    border-left: 2px solid var(--border);
    border-right: 2px solid var(--border);
    display: flex;
    align-items: center;
    justify-content: center;
    font-size: 38px;
    color: var(--ink);
  }
  .total-amount {
    position: absolute;
    right: 80px;
    top: 2398px;
    font-size: 80px;
    line-height: 92px;
    font-weight: 600;
    color: var(--ink);
  }

  .action-button {
    position: absolute;
    top: 2535px;
    height: 107px;
    width: 425px;
    border-radius: 5px;
    display: flex;
    align-items: center;
    justify-content: center;
    gap: 18px;
    font-size: 31px;
    font-weight: 700;
    letter-spacing: 0.5px;
  }
  .action-button--cart {
    left: 80px;
    background: var(--button-light);
    border: 3px solid var(--ink);
    color: var(--ink);
  }
  .action-button--cart svg { width: 40px; height: 40px; }
  .action-button--checkout {
    left: 535px;
    background: var(--button-dark);
    color: #ffffff;
  }
</style>
</head>
<body>
  <article class="product-card">
    <div class="product-media" role="img" aria-label="Wheel shown half in factory silver finish and half powder coated gloss black">
      <span class="media-label media-label--before">Before</span>
      <span class="media-label media-label--after">After</span>
    </div>

    <p class="block product-category">BLACKOUT</p>
    <h1 class="block product-title">Powder Coat Wheels - 4 Wheels</h1>
    <p class="block product-part">Part No: PCOATWHEELS4</p>

    <div class="block product-price">
      <span class="price-current">$499</span>
      <span class="price-original">$899</span>
    </div>

    <p class="block product-description">Blackout your factory Wheels by powder coating to delete chrome or to get an aggressive look to your new vehicle. Powder coated surfaces are more resistant to chipping, scratching, fading, and wearing than other finishes.</p>

    <ul class="block feature-list">
      <li>Chrome Delete</li>
      <li>Protects Factory</li>
      <li>Does Not Fade or Crack</li>
    </ul>

    <div class="block product-rating">
      <div class="rating-stars" aria-label="5 out of 5 stars">
        <svg viewBox="0 0 24 23"><path fill="var(--star)" d="M12 0l3.1 7.6 8.2.6-6.3 5.3 2 8L12 17.2 5 21.5l2-8L.7 8.2l8.2-.6z"/></svg>
        <svg viewBox="0 0 24 23"><path fill="var(--star)" d="M12 0l3.1 7.6 8.2.6-6.3 5.3 2 8L12 17.2 5 21.5l2-8L.7 8.2l8.2-.6z"/></svg>
        <svg viewBox="0 0 24 23"><path fill="var(--star)" d="M12 0l3.1 7.6 8.2.6-6.3 5.3 2 8L12 17.2 5 21.5l2-8L.7 8.2l8.2-.6z"/></svg>
        <svg viewBox="0 0 24 23"><path fill="var(--star)" d="M12 0l3.1 7.6 8.2.6-6.3 5.3 2 8L12 17.2 5 21.5l2-8L.7 8.2l8.2-.6z"/></svg>
        <svg viewBox="0 0 24 23"><path fill="var(--star)" d="M12 0l3.1 7.6 8.2.6-6.3 5.3 2 8L12 17.2 5 21.5l2-8L.7 8.2l8.2-.6z"/></svg>
      </div>
      <span class="rating-count">89 reviews</span>
    </div>

    <span class="purchase-label purchase-label--quantity">QUANTITY</span>
    <span class="purchase-label purchase-label--total">TOTAL</span>

    <div class="quantity-stepper">
      <span class="stepper-button" aria-label="Decrease">
        <svg viewBox="0 0 24 24"><path d="M4 12h16" stroke="var(--ink)" stroke-width="2.6" stroke-linecap="round"/></svg>
      </span>
      <span class="stepper-value">2</span>
      <span class="stepper-button" aria-label="Increase">
        <svg viewBox="0 0 24 24"><path d="M4 12h16M12 4v16" stroke="var(--ink)" stroke-width="2.6" stroke-linecap="round"/></svg>
      </span>
    </div>
    <span class="total-amount">$998</span>

    <span class="action-button action-button--cart">ADD TO CART
      <svg viewBox="0 0 24 24"><path fill="var(--ink)" d="M7 18a2 2 0 1 0 0 4 2 2 0 0 0 0-4zm10 0a2 2 0 1 0 0 4 2 2 0 0 0 0-4zM1 2v2h2l3.6 7.6-1.4 2.4c-.5 1 .2 2 1.3 2H19v-2H7.4l1.1-2h7.5c.8 0 1.4-.4 1.7-1l3.6-6.5L19.6 3H5.2l-.9-1z"/></svg>
    </span>
    <span class="action-button action-button--checkout">CHECKOUT</span>
  </article>
</body>
</html>
```